Brightmoor - a website to encourage people to spend time in nature

I have a squarespace site with some content on it but the squarespace template doesn't completely suit my needs, I keep fiddling with the template but actually I need some professional help to get it looking the way I want and with the right 'mood'.
The website is for "Brightmoor" - it will be a blog where I write about the importance of nature for good health. I also want to use the website to market services such as outdoor coaching, retreats and walking workshops.
This has been in my head for a LONG time and I currently only use instagram for micro-blogs but it's time for me to get this moving. I've previously engaged other designers on branding for it but they just didn't get it quite the way that I wanted it and I wasn't completely happy with the results. It's been a process for me as to what I want but in the meantime I just didn't come back to the design aspect of it now. I'm looking for a designer who understands the purpose of the website, the ethos and can help me realise this into a design that's clean, clear and simple.

Please note that I have a domain (brightmoor.org) and a lot of content drafted on squarespace already. I have published it with password protection - password is brightmoor2020 - it still has some of the original template on it, but does have some content. Don't take it as anything to follow in particular, i am looking for fresh eyes and fresh ideas.

Target Market(s)

There are three main groups that I want to target - people who are suffering from stress and anxiety, people who treat them and parents who want to get their kids outside (thereby preventing stress and anxiety)

Contact Information for Business Card

Joan Petrie
Brightmoor
Telephone +44 7700 900417
brightmoor@mailvane.com

Logo Text

Brightmoor - if that. I have an idea that the logo should have a leaf on it somewhere, or maybe just be a leaf.

Coding

Coded - Design and coding required

Number of Pages Required

5+ page

Font styles to use
Serif
Sans Serif

Colors
add136
33b8a4
34a6d7
3377b5

Requirements
Must have
• Space for lots of images. The ability for me to edit the pages if I need to. Be user friendly. Look beautiful.
• For an idea of the images I use and the content I'm interested in writing about have a look at @brightmoor on instagram.
• That pop up about cookies so I am complying with data laws.
Should not have
• Must not be too 'busy' I'd like to avoid too much movement.

```html
<!DOCTYPE html>
<html lang="en">
<head>
<meta charset="utf-8">
<title>Brightmoor – Home</title>
<link rel="stylesheet" href="https://fonts.googleapis.com/css2?family=Marcellus&family=Mulish:wght@400;600;700&family=Lobster+Two:ital,wght@1,700&display=swap">
<style>
:root{
  --lime:#add136;
  --lime-dark:#8cb52a;
  --teal:#33b8a4;
  --teal-dark:#1c9a86;
  --sky:#34a6d7;
  --navy:#3377b5;
  --ink:#222;
  --body:#555;
  --footer:#2e2e2e;
  --footer-deep:#1b1b1b;
  --white:#fff;
  --accent-sub:#dbee7a;
}
*{box-sizing:border-box;margin:0;padding:0}
html,body{width:786px;height:1200px;overflow:hidden;background:var(--white)}
body{position:relative;font-family:"Mulish",Arial,sans-serif}

.page{position:absolute;top:20px;width:730px;height:2300px;transform:scale(.5);transform-origin:0 0;background:var(--white);overflow:hidden}
.page--consent{left:18px}
.page--open{left:397px}

.serif{font-family:"Marcellus",Georgia,serif;font-weight:400}
.abs{position:absolute}

/* hero */
.hero{position:absolute;left:0;top:0;width:730px;height:406px;background:linear-gradient(180deg,#2a3323 0%,#3f5530 35%,#6f8a3c 65%,#8d9a55 100%)}
.brand{position:absolute;left:55px;top:14px;display:flex;align-items:center;gap:8px;color:var(--white);font-family:"Marcellus",Georgia,serif;font-size:20px}
.brand__dot{width:10px;height:10px;border-radius:50%;background:var(--lime)}
.nav{position:absolute;top:20px;left:376px;display:flex;gap:29px;font-size:10px;color:var(--white)}
.hero__title{position:absolute;left:55px;top:150px;font-size:31px;color:var(--white)}
.hero__text{position:absolute;left:55px;top:190px;width:300px;font-size:8.5px;line-height:18.5px;color:var(--white);text-align:justify}
.hero .btn{left:55px;top:274px}

/* buttons */
.btn{position:absolute;width:110px;height:28px;border-radius:14px;display:flex;align-items:center;justify-content:center;gap:5px;font-size:9.5px;font-weight:700}
.btn--lime{background:linear-gradient(180deg,#c8e24c,var(--lime-dark));color:#1d2a0c}
.btn--teal{background:linear-gradient(180deg,#45c8b1,var(--teal-dark));color:var(--white)}
.btn svg{width:9px;height:9px}

/* welcome */
.welcome__title{position:absolute;left:0;top:438px;width:730px;text-align:center;font-size:24px;color:var(--ink)}
.welcome__title span{color:var(--teal)}
.welcome__text{position:absolute;left:125px;top:468px;width:480px;text-align:center;font-size:9.5px;line-height:22px;color:#444}

/* feature bands */
.band{position:absolute;left:0;width:730px;height:299px}
.band__photo{position:absolute;inset:0}
.band--coaching .band__photo{background:linear-gradient(180deg,#6fa9a9 0%,#5e9ea5 45%,#4a7fa7 70%,#3e5fb0 85%,#2f5a7e 100%)}
.band--retreat .band__photo{background:radial-gradient(ellipse at 55% 45%,#4d7a55 0%,#2f5238 55%,#1f3526 100%)}
.band__title{position:absolute;left:0;top:68px;width:730px;text-align:center;font-size:32px;color:var(--white)}
.band__sub{position:absolute;left:0;top:111px;width:730px;text-align:center;font-family:"Lobster Two",Georgia,serif;font-style:italic;font-weight:700;font-size:14px;color:var(--accent-sub)}
.band__text{position:absolute;left:85px;top:136px;width:560px;text-align:center;font-size:9.5px;line-height:20px;color:var(--white)}
.band .btn{left:310px;top:201px}

/* gallery + columns */
.thumb{position:absolute;top:965px;width:201px;height:139px}
.thumb--beach{left:55px;background:linear-gradient(180deg,#8fb2d6 0%,#b7c8d6 30%,#6d6657 45%,#4d463c 100%)}
.thumb--sea{left:264px;background:linear-gradient(180deg,#9dc3e6 0%,#c9dcea 55%,#7e8a8e 75%,#5a605c 100%)}
.thumb--blossom{left:474px;background:radial-gradient(circle at 40% 40%,#f6b9c9 0%,#e06b8f 55%,#b8406a 100%)}
.copy{position:absolute;top:1118px;width:300px;font-size:8.5px;line-height:19px;color:var(--body);text-align:justify}
.copy--a{left:55px}.copy--b{left:375px}
.page .btn--view{left:310px;top:1208px}

/* team */
.member{position:absolute;top:1640px;width:201px}
.member--a{left:55px}.member--b{left:264px}.member--c{left:474px}
.member__name{font-family:"Marcellus",Georgia,serif;font-size:19px;letter-spacing:1px;color:var(--ink)}
.member__role{margin-top:10px;font-size:8.5px;font-weight:700;color:#333;letter-spacing:.3px}
.member__bio{margin-top:8px;font-size:8.5px;line-height:17.5px;color:var(--body);text-align:justify}
.scene{position:absolute;top:1809px;width:297px;height:216px}
.scene--path{left:55px;background:linear-gradient(180deg,#9aa67a 0%,#5f6b3e 40%,#8d7a86 75%,#7c6a72 100%)}
.scene--bluebell{left:375px;background:linear-gradient(180deg,#a9b98e 0%,#55683c 45%,#6a5bb2 72%,#4a3f8a 100%)}

/* footer */
.footer{position:absolute;left:0;top:2060px;width:730px;height:206px;background:var(--footer);color:var(--white)}
.footer__col{position:absolute;top:44px}
.footer__col h4{font-size:14px;font-weight:600;margin-bottom:12px}
.footer__col li{list-style:none;font-size:8px;line-height:16.5px}
.footer__col p{font-size:8px;line-height:16.5px}
.footer__col a{color:var(--white)}
.col-links{left:55px}.col-legal{left:166px}.col-contact{left:294px}.col-news{left:506px}
.subscribe{margin-top:10px;width:170px;height:22px;border-radius:11px;background:var(--white);position:relative;border:1px solid var(--lime)}
.subscribe span{position:absolute;left:10px;top:6px;font-size:6.5px;color:#888}
.subscribe b{position:absolute;right:0;top:0;width:67px;height:20px;border-radius:10px;background:linear-gradient(180deg,#c8e24c,var(--lime-dark));color:#1d2a0c;font-size:8px;font-weight:600;display:flex;align-items:center;justify-content:center}
.social{display:flex;gap:9px;margin-top:12px}
.social i{width:9px;height:9px;border-radius:50%;background:var(--white)}
.hours{position:absolute;left:0;top:180px;width:730px;text-align:center;font-size:8px}
.legal-bar{position:absolute;left:0;top:2266px;width:730px;height:34px;background:var(--footer-deep);color:var(--white);font-size:7.5px;display:flex;align-items:center;justify-content:center}

/* consent */
.dim{position:absolute;inset:0;background:rgba(70,70,70,.5)}
.consent{position:absolute;left:196px;top:78px;width:336px;height:336px;border-radius:50%;border:5px solid var(--lime);background:linear-gradient(180deg,#74dccb 0%,#33b8a4 50%,#148a72 100%);text-align:center;color:var(--white)}
.consent__name{margin-top:76px;font-family:"Marcellus",Georgia,serif;font-size:31px}
.consent__text{margin:20px auto 0;width:262px;font-size:8.5px;line-height:19px;color:#0f2e28}
.consent__btn{display:block;margin:9px auto 0;width:240px;height:28px;line-height:28px;font-size:10px;font-weight:600;letter-spacing:.5px}
.consent__btn--accept{margin-top:10px;background:linear-gradient(180deg,#5cc3ee,var(--sky) 50%,#2382b8)}
.consent__btn--setting{background:linear-gradient(180deg,#4c8fd0,var(--navy) 50%,#1f4e8a)}
</style>
</head>
<body>

<svg width="0" height="0" style="position:absolute">
  <symbol id="arrow" viewBox="0 0 10 10"><circle cx="5" cy="5" r="5" fill="currentColor"/><path d="M3 5h4M5.2 3.2 7 5 5.2 6.8" stroke="#fff" stroke-width="1.2" fill="none"/></symbol>
</svg>

<!-- ========== page with consent prompt ========== -->
<section class="page page--consent">
  <header class="hero">
    <div role="img" aria-label="Forest path in morning light" class="abs" style="inset:0"></div>
    <div class="brand"><span>Brightmoor</span><span class="brand__dot"></span></div>
    <nav class="nav"><span>Home</span><span>About Us</span><span>Our Blog</span><span>Gallery</span><span>Contact Us</span></nav>
    <h1 class="hero__title serif">Brightmoor</h1>
    <p class="hero__text">Our modern way of living doesn't always allow for connection to nature on an everyday basis. The pressures of modern life and our way of living it means we spend too much time indoors, at home, in the office, in schools, in the car.</p>
    <span class="btn btn--lime">Learn More <svg><use href="#arrow"/></svg></span>
  </header>

  <h2 class="welcome__title serif">Welcome To <span>BRIGHTMOOR WALKING</span></h2>
  <p class="welcome__text">Brightmoor Walking is an initiative aimed at getting people back into nature in the most gentlest of ways - by taking a walk with friends in the great outdoors. The concept is simple - schedule a walk outside, once a week with two or three other people. That's it. Sometimes the best things are the simplest and here's why this</p>
  <span class="btn btn--lime" style="left:251px;top:564px">Learn More <svg><use href="#arrow"/></svg></span>
  <span class="btn btn--teal" style="left:369px;top:564px">Contact Us <svg><use href="#arrow"/></svg></span>

  <section class="band band--coaching" style="top:629px">
    <div class="band__photo" role="img" aria-label="Misty woodland with bluebells"></div>
    <h3 class="band__title serif">Coaching</h3>
    <p class="band__sub">Sed ut perspiciatis unde omnis iste natus error sit voluptatem</p>
    <p class="band__text">Only one thing better than coaching and that's coaching in the great outdoors. We believe that being out in nature gives you a greater sense of perspective when working through issues and figuring out life's path. We are part of nature, not apart from it.</p>
    <span class="btn btn--lime">Learn More <svg><use href="#arrow"/></svg></span>
  </section>

  <div class="thumb thumb--beach" role="img" aria-label="Dog on a beach at low tide"></div>
  <div class="thumb thumb--sea" role="img" aria-label="Child looking out to sea"></div>
  <div class="thumb thumb--blossom" role="img" aria-label="Pink cherry blossom"></div>
  <p class="copy copy--a">Sed ut perspiciatis unde omnis iste natus error sit voluptatem accusantium doloremque laudantium, totam rem aperiam, eaque ipsa quae ab illo inventore veritatis et quasi architecto beatae vitae dicta sunt explicabo. Nemo enim ipsam voluptatem quia voluptas sit sequi nesciunt.</p>
  <p class="copy copy--b">Sed ut perspiciatis unde omnis iste natus error sit voluptatem accusantium doloremque laudantium, totam rem aperiam, eaque ipsa quae ab illo inventore veritatis et quasi architecto beatae vitae dicta sunt explicabo. Nemo enim ipsam voluptatem quia voluptas sit sequi nesciunt.</p>
  <span class="btn btn--teal btn--view">View More <svg><use href="#arrow"/></svg></span>

  <section class="band band--retreat" style="top:1296px">
    <div class="band__photo" role="img" aria-label="Ladybird on a green leaf"></div>
    <h3 class="band__title serif">Retera</h3>
    <p class="band__sub">Sed ut perspiciatis unde omnis iste natus error sit voluptatem</p>
    <p class="band__text">Sometimes you just need to get away from it all. And that's where Brightmoor retreats come in. Our retreats are based at Heathercombe Cottage located at the foot of the Carrow Hills in beautiful Northern Ireland. Typically 2/3 days that involve restoring your connection to the natural world in stunning surroundings.</p>
    <span class="btn btn--teal">View More <svg><use href="#arrow"/></svg></span>
  </section>

  <div class="member member--a"><h4 class="member__name">Nora Keld</h4><p class="member__role">LOREM IPSUM DOLOR SIT AMET</p><p class="member__bio">Lorem ipsum dolor sit amet, tetur adipiscing elit, sed do eiusmod tempor incididunt ut labore et dolore magna aliqua. Ut enim ad minim veniam, quis nostrud tion ullamco laboris nisi ut aliquip ex ea commodo consequat.</p></div>
  <div class="member member--b"><h4 class="member__name">Elio Marsh</h4><p class="member__role">LOREM IPSUM DOLOR SIT AMET</p><p class="member__bio">Lorem ipsum dolor sit amet, tetur adipiscing elit, sed do eiusmod tempor incididunt ut labore et dolore magna aliqua. Ut enim ad minim veniam, quis nostrud tion ullamco laboris nisi ut aliquip ex ea commodo consequat.</p></div>
  <div class="member member--c"><h4 class="member__name">Ruth Calloway</h4><p class="member__role">LOREM IPSUM DOLOR SIT AMET</p><p class="member__bio">Lorem ipsum dolor sit amet, tetur adipiscing elit, sed do eiusmod tempor incididunt ut labore et dolore magna aliqua. Ut enim ad minim veniam, quis nostrud tion ullamco laboris nisi ut aliquip ex ea commodo consequat.</p></div>

  <div class="scene scene--path" role="img" aria-label="Woodland path between trees"></div>
  <div class="scene scene--bluebell" role="img" aria-label="Bluebell woods"></div>

  <footer class="footer">
    <div class="footer__col col-links"><h4>Links</h4><ul><li>Home</li><li>About</li><li>Gallery</li><li>Our Blog</li><li>Contact Us</li></ul></div>
    <div class="footer__col col-legal"><h4>Legal</h4><ul><li>Faq</li><li>Privacy Policy</li><li>Terms of Use</li><li>Testimonials</li></ul></div>
    <div class="footer__col col-contact"><h4>Contact Us</h4><p>18 Alder Row, Fernhill,<br>NY 12990 <u>(Get Direction)</u><br>Phone: 555 014 2277<br>Email: info@brightmoor.org</p></div>
    <div class="footer__col col-news"><h4>Newsletter</h4><p>Subscribe Our Newsletter For More Info</p><div class="subscribe"><span>Email Address</span><b>Subscribe</b></div><div class="social"><i></i><i></i><i></i><i></i><i></i></div></div>
    <p class="hours">Opening Hours : Monday – Friday, 8:00 a.m. – 5:00 p.m.</p>
  </footer>
  <div class="legal-bar">© 2020 Copyrights.The Company Name.All Rights Reserved</div>

  <div class="dim"></div>
  <aside class="consent" aria-label="Cookie consent">
    <p class="consent__name">Brightmoor</p>
    <p class="consent__text">Lorem ipsum dolor sit amet, consectetur adipiscing elit, sed do eiusmod tempor incididunt ut labore et dolore magna aliqua. Quis ipsum suspendisse ultrices gravida.</p>
    <span class="consent__btn consent__btn--accept">ACCEPT</span>
    <span class="consent__btn consent__btn--setting">SETTING</span>
  </aside>
</section>

<!-- ========== page without prompt ========== -->
<section class="page page--open">
  <header class="hero">
    <div role="img" aria-label="Forest path in morning light" class="abs" style="inset:0"></div>
    <div class="brand"><span>Brightmoor</span><span class="brand__dot"></span></div>
    <nav class="nav"><span>Home</span><span>About Us</span><span>Our Blog</span><span>Gallery</span><span>Contact Us</span></nav>
    <h1 class="hero__title serif">Brightmoor</h1>
    <p class="hero__text">Our modern way of living doesn't always allow for connection to nature on an everyday basis. The pressures of modern life and our way of living it means we spend too much time indoors, at home, in the office, in schools, in the car.</p>
    <span class="btn btn--lime">Learn More <svg><use href="#arrow"/></svg></span>
  </header>

  <h2 class="welcome__title serif">Welcome To <span>BRIGHTMOOR WALKING</span></h2>
  <p class="welcome__text">Brightmoor Walking is an initiative aimed at getting people back into nature in the most gentlest of ways - by taking a walk with friends in the great outdoors. The concept is simple - schedule a walk outside, once a week with two or three other people. That's it. Sometimes the best things are the simplest and here's why this</p>
  <span class="btn btn--lime" style="left:251px;top:564px">Learn More <svg><use href="#arrow"/></svg></span>
  <span class="btn btn--teal" style="left:369px;top:564px">Contact Us <svg><use href="#arrow"/></svg></span>

  <section class="band band--coaching" style="top:629px">
    <div class="band__photo" role="img" aria-label="Misty woodland with bluebells"></div>
    <h3 class="band__title serif">Coaching</h3>
    <p class="band__sub">Sed ut perspiciatis unde omnis iste natus error sit voluptatem</p>
    <p class="band__text">Only one thing better than coaching and that's coaching in the great outdoors. We believe that being out in nature gives you a greater sense of perspective when working through issues and figuring out life's path. We are part of nature, not apart from it.</p>
    <span class="btn btn--lime">Learn More <svg><use href="#arrow"/></svg></span>
  </section>

  <div class="thumb thumb--beach" role="img" aria-label="Dog on a beach at low tide"></div>
  <div class="thumb thumb--sea" role="img" aria-label="Child looking out to sea"></div>
  <div class="thumb thumb--blossom" role="img" aria-label="Pink cherry blossom"></div>
  <p class="copy copy--a">Sed ut perspiciatis unde omnis iste natus error sit voluptatem accusantium doloremque laudantium, totam rem aperiam, eaque ipsa quae ab illo inventore veritatis et quasi architecto beatae vitae dicta sunt explicabo. Nemo enim ipsam voluptatem quia voluptas sit sequi nesciunt.</p>
  <p class="copy copy--b">Sed ut perspiciatis unde omnis iste natus error sit voluptatem accusantium doloremque laudantium, totam rem aperiam, eaque ipsa quae ab illo inventore veritatis et quasi architecto beatae vitae dicta sunt explicabo. Nemo enim ipsam voluptatem quia voluptas sit sequi nesciunt.</p>
  <span class="btn btn--teal btn--view">View More <svg><use href="#arrow"/></svg></span>

  <section class="band band--retreat" style="top:1296px">
    <div class="band__photo" role="img" aria-label="Ladybird on a green leaf"></div>
    <h3 class="band__title serif">Retera</h3>
    <p class="band__sub">Sed ut perspiciatis unde omnis iste natus error sit voluptatem</p>
    <p class="band__text">Sometimes you just need to get away from it all. And that's where Brightmoor retreats come in. Our retreats are based at Heathercombe Cottage located at the foot of the Carrow Hills in beautiful Northern Ireland. Typically 2/3 days that involve restoring your connection to the natural world in stunning surroundings.</p>
    <span class="btn btn--teal">View More <svg><use href="#arrow"/></svg></span>
  </section>

  <div class="member member--a"><h4 class="member__name">Nora Keld</h4><p class="member__role">LOREM IPSUM DOLOR SIT AMET</p><p class="member__bio">Lorem ipsum dolor sit amet, tetur adipiscing elit, sed do eiusmod tempor incididunt ut labore et dolore magna aliqua. Ut enim ad minim veniam, quis nostrud tion ullamco laboris nisi ut aliquip ex ea commodo consequat.</p></div>
  <div class="member member--b"><h4 class="member__name">Elio Marsh</h4><p class="member__role">LOREM IPSUM DOLOR SIT AMET</p><p class="member__bio">Lorem ipsum dolor sit amet, tetur adipiscing elit, sed do eiusmod tempor incididunt ut labore et dolore magna aliqua. Ut enim ad minim veniam, quis nostrud tion ullamco laboris nisi ut aliquip ex ea commodo consequat.</p></div>
  <div class="member member--c"><h4 class="member__name">Ruth Calloway</h4><p class="member__role">LOREM IPSUM DOLOR SIT AMET</p><p class="member__bio">Lorem ipsum dolor sit amet, tetur adipiscing elit, sed do eiusmod tempor incididunt ut labore et dolore magna aliqua. Ut enim ad minim veniam, quis nostrud tion ullamco laboris nisi ut aliquip ex ea commodo consequat.</p></div>

  <div class="scene scene--path" role="img" aria-label="Woodland path between trees"></div>
  <div class="scene scene--bluebell" role="img" aria-label="Bluebell woods"></div>

  <footer class="footer">
    <div class="footer__col col-links"><h4>Links</h4><ul><li>Home</li><li>About</li><li>Gallery</li><li>Our Blog</li><li>Contact Us</li></ul></div>
    <div class="footer__col col-legal"><h4>Legal</h4><ul><li>Faq</li><li>Privacy Policy</li><li>Terms of Use</li><li>Testimonials</li></ul></div>
    <div class="footer__col col-contact"><h4>Contact Us</h4><p>18 Alder Row, Fernhill,<br>NY 12990 <u>(Get Direction)</u><br>Phone: 555 014 2277<br>Email: info@brightmoor.org</p></div>
    <div class="footer__col col-news"><h4>Newsletter</h4><p>Subscribe Our Newsletter For More Info</p><div class="subscribe"><span>Email Address</span><b>Subscribe</b></div><div class="social"><i></i><i></i><i></i><i></i><i></i></div></div>
    <p class="hours">Opening Hours : Monday – Friday, 8:00 a.m. – 5:00 p.m.</p>
  </footer>
  <div class="legal-bar">© 2020 Copyrights.The Company Name.All Rights Reserved</div>
</section>

</body>
</html>
```